Creative Web design for Tattoo Artist

I am a tattoo artist with a private tattoo/art studio in Spring, TX. I need to design a website for my studio, to include the following "pages" :
-home/about
-FAQ
-Gallery
-Inquiries
-shop
We would like to see designs that are more dark or "moody", and like the colors black/gold.
I'd like my website to reflect my studio, an award winning private, upscale custom only tattoo studio.

I've attached some examples of styles we liked.

Target Market(s)

adults ages 18-50, interested in tattoos, or fine art

Industry/Entity Type

Tattoos/Fine Art/Arts

Coding

Coded - Design and coding required

Number of Pages Required

5+ page

Colors

Designer to choose colors to be used in the design.

Requirements
Must have
• gallery section, and e-commerce page set up so I can begin selling merchandise, I'd like the fonts to flow with my logo design

```html
<!DOCTYPE html>
<html lang="en">
<head>
<meta charset="utf-8">
<title>The Gilded Viper — Tattoo Studio</title>
<link href="https://fonts.googleapis.com/css2?family=Merriweather:wght@300;400;700;900&display=swap" rel="stylesheet">
<style>
:root{
  --gold:#b8900f;
  --gold-text:#c79b1f;
  --ink:#161616;
  --ink-deep:#111111;
  --white:#ffffff;
  --muted:#d8d8d8;
  --line:#bdbdbd;
}
*{margin:0;padding:0;box-sizing:border-box}
html,body{width:1200px;height:4051px;overflow:hidden}
body{position:relative;background:var(--ink);color:var(--white);font-family:"Merriweather",Georgia,serif}
.abs{position:absolute}
a{color:inherit;text-decoration:none}

/* top bar */
.topbar{left:0;top:0;width:1200px;height:30px;background:var(--gold);font-size:11px;font-weight:700;display:flex;align-items:center}
.topbar .info{position:absolute;display:flex;align-items:center;gap:6px}
.topbar .socials{position:absolute;right:110px;top:8px;display:flex;gap:14px}
.topbar .socials span{width:13px;height:13px;border-radius:50%;background:var(--white)}

/* hero */
.hero{left:0;top:30px;width:1200px;height:481px;background:radial-gradient(ellipse at 35% 35%,#5a5a5a 0%,#2e2e2e 45%,#141414 100%)}
.brand{font-weight:900;color:var(--white);font-size:15px;line-height:1.15;text-align:center;letter-spacing:1px}
.brand-hero{left:108px;top:80px;width:92px}
.nav{top:64px;left:626px;display:flex;gap:37px;font-size:15px;font-weight:700}
.nav .active{text-decoration:underline;text-underline-offset:6px}
.cart{left:1057px;top:60px}
.hero-kicker{left:112px;top:260px;font-size:29px;font-weight:400}
.hero-title{left:112px;top:300px;font-size:49px;font-weight:900;letter-spacing:.5px}
.btn{background:var(--gold);color:var(--white);font-size:12px;font-weight:700;display:flex;align-items:center;justify-content:center;letter-spacing:.3px}
.btn-book{left:113px;top:377px;width:123px;height:41px}
.slider-ind{left:1120px;top:198px;width:50px;height:135px}

/* about */
.about-photo{left:112px;top:595px;width:462px;height:301px;background:linear-gradient(120deg,#8a8a8a,#3c3c3c 55%,#1c1c1c)}
.about-title{left:604px;top:600px;font-size:38px;font-weight:700;color:var(--gold-text);line-height:1.12;width:520px}
.about-lead{left:605px;top:695px;width:460px;font-size:14px;font-weight:900;line-height:1.5}
.about-body{left:605px;top:740px;width:460px;font-size:12.5px;line-height:1.6;color:var(--muted)}
.btn-learn{left:607px;top:841px;width:134px;height:43px}
.faint-name{color:#2c2c2c;font-weight:900;font-size:20px;text-align:center;line-height:1.1}

/* section titles */
.section-title{left:0;width:1200px;text-align:center;font-size:38px;font-weight:700;color:var(--gold-text);text-decoration:underline;text-decoration-thickness:2px;text-underline-offset:8px}
.section-text{left:0;width:1200px;text-align:center;font-size:15px;line-height:1.6;color:var(--white)}

/* shop */
.product{background:#cfcfcf}
.p-shirt{left:112px;top:1194px;width:297px;height:308px;background:linear-gradient(#d6d6d6,#c4c4c4)}
.p-cup{left:434px;top:1165px;width:332px;height:350px;background:linear-gradient(150deg,#f4f4f4,#cfcfcf)}
.p-hood{left:791px;top:1194px;width:297px;height:308px;background:linear-gradient(#d6d6d6,#c4c4c4)}
.arrow-btn{top:1354px;width:34px;height:65px;background:var(--gold);display:flex;align-items:center;justify-content:center}
.p-name{width:297px;text-align:center;font-size:25px;font-weight:900}
.p-price{width:297px;text-align:center;font-size:20px}
.btn-buy{width:134px;height:43px;top:1612px}

/* gallery */
.tabs{top:1928px;left:0;width:1200px;display:flex;justify-content:center;gap:53px;font-size:16px;font-weight:700}
.tabs .active{text-decoration:underline;text-underline-offset:6px}
.g-big{left:112px;top:1984px;width:486px;height:423px;background:radial-gradient(ellipse at 60% 40%,#6a6a6a,#2b2b2b 70%,#1a1a1a)}
.g-frame{left:124px;top:1996px;width:462px;height:403px;border:1px solid var(--gold)}
.g-label{left:112px;top:2168px;width:474px;text-align:center;font-size:28px;font-weight:900}
.g-tile{width:225px;height:206px;background:linear-gradient(135deg,#c9c9c9,#6e6e6e)}
.btn-view{left:532px;top:2455px;width:135px;height:42px}

/* inquiry */
.field{border:1px solid var(--line);font-size:12.5px;font-weight:700;color:var(--white);padding:17px 19px}
.btn-submit{left:532px;top:3166px;width:135px;height:43px}

/* map */
.map{left:0;top:3296px;width:1200px;height:519px;background:linear-gradient(135deg,#e6e6e6,#d2d2d2 60%,#dcdcdc)}

/* footer */
.footer{left:0;top:3815px;width:1200px;height:236px;background:var(--ink-deep)}
.brand-foot{left:108px;top:3900px;width:100px}
.foot-nav{left:253px;top:3877px;display:flex;gap:40px;font-size:16px;font-weight:700}
.foot-nav .active{text-decoration:underline;text-underline-offset:6px}
.copy{left:0;width:1196px;top:3967px;text-align:center;font-size:12.5px;font-weight:700}
</style>
</head>
<body>

<!-- top bar -->
<div class="abs topbar">
  <div class="info" style="left:112px">
    <svg width="14" height="14" viewBox="0 0 24 24" fill="none" stroke="#fff" stroke-width="2"><path d="M5 3h4l2 5-3 2a12 12 0 0 0 6 6l2-3 5 2v4a2 2 0 0 1-2 2A18 18 0 0 1 3 5a2 2 0 0 1 2-2z"/></svg>
    <span>Call us: (555) 010-2244</span>
  </div>
  <div class="info" style="left:314px">
    <svg width="14" height="14" viewBox="0 0 24 24" fill="none" stroke="#fff" stroke-width="2"><circle cx="12" cy="12" r="9"/><path d="M12 7v5l3 2"/></svg>
    <span>Opening Hours: Mon-Fri: 10 am-8 pm</span>
  </div>
  <div class="socials"><span></span><span></span><span></span><span></span></div>
</div>

<!-- hero -->
<section class="abs hero" role="img" aria-label="Black and white photo of a tattoo artist's gloved hand working with a tattoo machine"></section>
<div class="abs brand brand-hero">THE<br>GILDED<br>VIPER</div>
<nav class="abs nav">
  <a class="active">Home</a><a>FAQ</a><a>Gallery</a><a>Inquiries</a><a>Shop</a>
</nav>
<svg class="abs cart" width="30" height="30" viewBox="0 0 30 30" fill="none" stroke="#fff" stroke-width="2">
  <path d="M2 7h4l3 12h13l3-9H8"/><circle cx="11" cy="24" r="1.8"/><circle cx="20" cy="24" r="1.8"/>
  <circle cx="24" cy="5" r="5" fill="#fff" stroke="none"/><text x="24" y="8" font-size="8" text-anchor="middle" fill="#161616" stroke="none" font-family="Merriweather,serif" font-weight="700">0</text>
</svg>
<div class="abs hero-kicker">WELCOME TO</div>
<h1 class="abs hero-title">THE GILDED VIPER</h1>
<a class="abs btn btn-book">BOOK NOW</a>
<svg class="abs slider-ind" viewBox="0 0 50 135" fill="none" stroke="#fff" stroke-width="1.5">
  <path d="M25 2v24M18 9l7-7 7 7"/>
  <circle cx="25" cy="67" r="23"/>
  <text x="25" y="72" font-size="13" text-anchor="middle" fill="#fff" stroke="none" font-family="Merriweather,serif">1 / 3</text>
  <path d="M25 109v24M18 126l7 7 7-7"/>
</svg>

<!-- about -->
<div class="abs about-photo" role="img" aria-label="Photo of a tattoo artist working on a client's back"></div>
<h2 class="abs about-title">WELCOME TO OUR<br>TATTOO STUDIO</h2>
<p class="abs about-lead">We have been numerously recognized as #1 tattoo studio and deliver the best tattooing services.</p>
<p class="abs about-body">Lorem Ipsum is simply dummy text of the printing and typesetting industry. Lorem Ipsum has been the industry's standard dummy text ever since the 1500s, when an unknown printer took a galley of type and scrambled it to make a type specimen book.</p>
<a class="abs btn btn-learn">LEARN MORE</a>
<div class="abs faint-name" style="left:1070px;top:850px;width:80px">GILDED<br>VIPER</div>

<!-- shop -->
<h2 class="abs section-title" style="top:1024px">SHOP</h2>
<p class="abs section-text" style="top:1092px">Lorem Ipsum is simply dummy text of the printing and typesetting industry. Lorem Ipsum has been the industry's<br>standard dummy text ever since the 1500s, when an unknown printer took a galley of type.</p>

<a class="abs arrow-btn" style="left:53px"><svg width="12" height="16" viewBox="0 0 12 16" fill="none" stroke="#fff" stroke-width="2.5"><path d="M9 2 3 8l6 6"/></svg></a>
<div class="abs p-shirt" role="img" aria-label="Photo of a black printed T-shirt"></div>
<div class="abs p-cup" role="img" aria-label="Photo of a white printed coffee mug"></div>
<div class="abs p-hood" role="img" aria-label="Photo of a black hoodie"></div>
<a class="abs arrow-btn" style="left:1113px"><svg width="12" height="16" viewBox="0 0 12 16" fill="none" stroke="#fff" stroke-width="2.5"><path d="M3 2l6 6-6 6"/></svg></a>

<div class="abs p-name" style="left:112px;top:1532px">T - Shirts</div>
<div class="abs p-price" style="left:112px;top:1570px">Price : $ 199.00</div>
<a class="abs btn btn-buy" style="left:193px">BUY NOW</a>

<div class="abs p-name" style="left:451px;top:1532px">Cups</div>
<div class="abs p-price" style="left:451px;top:1570px">Price : $ 99.00</div>
<a class="abs btn btn-buy" style="left:532px">BUY NOW</a>

<div class="abs p-name" style="left:791px;top:1532px">Hoodies</div>
<div class="abs p-price" style="left:791px;top:1570px">Price : $ 299.00</div>
<a class="abs btn btn-buy" style="left:872px">BUY NOW</a>

<!-- gallery -->
<h2 class="abs section-title" style="top:1780px">GALLERY</h2>
<p class="abs section-text" style="top:1857px">Our studio provides tattoos of various complexity. From simple to highly creative artworks.We do <b>'Custom Tatoo'</b><br>contact us for more details. Take a look at the gallery below to discover our best works.</p>
<div class="abs tabs">
  <a class="active">ALL</a><a>TRADITIONAL TATTOOS</a><a>ORNAMENT TATTOOS</a><a>MINIMALISTIC</a><a>OTHER</a>
</div>
<div class="abs g-big" role="img" aria-label="Photo of an artist tattooing a serpent design on an arm"></div>
<div class="abs g-frame"></div>
<div class="abs g-label">Surrealism</div>
<svg class="abs" style="left:534px;top:2350px" width="52" height="49" viewBox="0 0 52 49"><path d="M52 0V49H0Z" fill="#b8900f"/><path d="M37 34h9M41.5 29.5v9" stroke="#fff" stroke-width="1.6"/></svg>
<div class="abs g-tile" style="left:617px;top:1984px" role="img" aria-label="Photo of a tattoo in progress with machine"></div>
<div class="abs g-tile" style="left:860px;top:1984px" role="img" aria-label="Photo of a rose tattoo on a shoulder blade"></div>
<div class="abs g-tile" style="left:617px;top:2207px" role="img" aria-label="Photo of a floral ornament tattoo being inked"></div>
<div class="abs g-tile" style="left:860px;top:2207px" role="img" aria-label="Photo of a sleeve tattoo next to a sketch"></div>
<a class="abs btn btn-view">VIEW ALL</a>

<!-- inquiry -->
<h2 class="abs section-title" style="top:2648px">INQUIRY</h2>
<p class="abs section-text" style="top:2721px;font-size:14px">Lorem Ipsum is simply dummy text of the printing and typesetting industry. Lorem Ipsum<br>has dummy text ever since the 1500s, when an unknown printer took a galley of type.</p>
<div class="abs faint-name" style="left:55px;top:3080px;width:110px;font-size:24px">GILDED<br>VIPER</div>
<div class="abs field" style="left:274px;top:2803px;width:314px;height:50px">First Name</div>
<div class="abs field" style="left:610px;top:2803px;width:315px;height:50px">Last Name</div>
<div class="abs field" style="left:274px;top:2872px;width:314px;height:51px">Email Address</div>
<div class="abs field" style="left:610px;top:2872px;width:315px;height:51px">Contact Number</div>
<div class="abs field" style="left:274px;top:2942px;width:651px;height:50px">Select a service...</div>
<svg class="abs" style="left:891px;top:2963px" width="12" height="8" viewBox="0 0 12 8" fill="none" stroke="#fff" stroke-width="1.6"><path d="M1 1l5 5 5-5"/></svg>
<div class="abs field" style="left:274px;top:3009px;width:651px;height:120px">Additional Message</div>
<a class="abs btn btn-submit">SUBMIT</a>

<!-- map -->
<div class="abs map" role="img" aria-label="Greyscale street map showing the studio location"></div>

<!-- footer -->
<footer class="abs footer"></footer>
<div class="abs brand brand-foot">THE<br>GILDED<br>VIPER</div>
<nav class="abs foot-nav">
  <a class="active">Home</a><a>FAQ</a><a>Gallery</a><a>Inquiries</a><a>Shop</a><a>Blogs</a><a>Newsletter</a><a>Contact Us</a>
</nav>
<div class="abs copy">© 2023 The Gilded Viper.&nbsp; All Rights Reserved Privacy Policy</div>

</body>
</html>
```